Harborline Auto LLC

Car Dealer Customer Service
Address: 2874 Cresthaven Road, Shelbyville, TN 37162
web: www.harborlineautoxq.net
email: harborlineautoxq@mailnest.example
Phone: (931) 555-0148
Phone: (629) 555-0173

```html
<!DOCTYPE html>
<html lang="en">
<head>
<meta charset="UTF-8">
<title>Harborline Auto – Business Card</title>
<link href="https://fonts.googleapis.com/css2?family=Montserrat:wght@700;800&family=Roboto:wght@400;500&display=swap" rel="stylesheet">
<style>
  :root {
    --bg: #2b2b2d;
    --blue-light: #2b98d3;
    --blue-dark: #1c77ad;
    --brand-blue: #1f73a8;
    --orange: #ebb145;
    --white: #ffffff;
  }
  * { margin: 0; padding: 0; box-sizing: border-box; }
  html, body { width: 1200px; height: 960px; overflow: hidden; }
  body {
    background: var(--bg);
    position: relative;
    font-family: "Roboto", sans-serif;
  }
  .card {
    position: absolute;
    left: 250px;
    width: 700px;
    height: 400px;
    border-radius: 26px;
    overflow: hidden;
    box-shadow: 0 16px 40px rgba(0,0,0,0.45);
  }
  .card-front {
    top: 50px;
    background: linear-gradient(180deg, var(--blue-light), var(--blue-dark));
    display: flex;
    align-items: center;
    justify-content: center;
  }
  .brand {
    display: flex;
    align-items: center;
    gap: 18px;
  }
  .brand-dot {
    width: 54px;
    height: 54px;
    border-radius: 50%;
    flex: none;
  }
  .brand-name {
    font-family: "Montserrat", sans-serif;
    font-weight: 800;
    letter-spacing: 1px;
    text-transform: uppercase;
    white-space: nowrap;
  }
  .card-front .brand-dot { background: var(--orange); }
  .card-front .brand-name { color: var(--white); font-size: 46px; }

  .card-back {
    top: 510px;
    background: var(--white);
  }
  .card-back .waves { position: absolute; inset: 0; }
  .card-back .brand {
    position: absolute;
    left: 44px;
    top: 150px;
    gap: 10px;
  }
  .card-back .brand-dot { width: 32px; height: 32px; background: var(--brand-blue); }
  .card-back .brand-name { color: var(--brand-blue); font-size: 27px; }

  .person {
    position: absolute;
    right: 48px;
    top: 30px;
    text-align: right;
  }
  .person-name {
    font-family: "Montserrat", sans-serif;
    font-weight: 700;
    font-size: 24px;
    color: var(--brand-blue);
    text-transform: uppercase;
  }
  .person-role {
    font-size: 15px;
    color: var(--orange);
    margin-top: 2px;
  }
  .contact {
    position: absolute;
    right: 34px;
    top: 172px;
    list-style: none;
    color: var(--white);
    font-size: 13px;
    line-height: 20px;
    text-align: right;
  }
  .contact li {
    display: flex;
    justify-content: flex-end;
    align-items: center;
    gap: 8px;
    white-space: nowrap;
  }
  .contact .icon { width: 12px; height: 12px; flex: none; }
  .contact .plain { padding-right: 20px; }
</style>
</head>
<body>

<section class="card card-front" aria-label="Card front">
  <div class="brand">
    <span class="brand-dot"></span>
    <span class="brand-name">Harborline Auto</span>
  </div>
</section>

<section class="card card-back" aria-label="Card back">
  <svg class="waves" viewBox="0 0 700 400" preserveAspectRatio="none" aria-hidden="true">
    <path d="M700,95 C600,92 500,100 452,170 C405,235 375,305 250,350 C170,375 80,380 0,384 L0,400 L700,400 Z" fill="var(--orange)"/>
    <path d="M700,84 C595,80 490,90 440,160 C395,228 362,300 240,342 C160,368 80,372 0,374" fill="none" stroke="var(--orange)" stroke-width="3"/>
    <path d="M440,122 C410,225 345,318 220,356" fill="none" stroke="var(--brand-blue)" stroke-width="3"/>
    <path d="M0,362 C90,358 160,354 230,346" fill="none" stroke="var(--orange)" stroke-width="5"/>
  </svg>

  <div class="brand">
    <span class="brand-dot"></span>
    <span class="brand-name">Harborline Auto</span>
  </div>

  <div class="person">
    <div class="person-name">Daniel Mercer</div>
    <div class="person-role">Founder &amp; CEO</div>
  </div>

  <ul class="contact">
    <li>2874 Cresthaven Road
      <svg class="icon" viewBox="0 0 12 12"><path d="M6 0.5a4 4 0 0 0-4 4c0 3 4 7 4 7s4-4 4-7a4 4 0 0 0-4-4z" fill="var(--white)"/><circle cx="6" cy="4.5" r="1.5" fill="var(--orange)"/></svg>
    </li>
    <li class="plain">Shelbyville, TN 37162</li>
    <li>(931) 555-0148
      <svg class="icon" viewBox="0 0 12 12"><path d="M2.5 1l2 0 1 2.5-1.3 1a6 6 0 0 0 3.3 3.3l1-1.3 2.5 1v2a1 1 0 0 1-1 1A9.5 9.5 0 0 1 1.5 2a1 1 0 0 1 1-1z" fill="var(--white)"/></svg>
    </li>
    <li>(629) 555-0173
      <svg class="icon" viewBox="0 0 12 12"><path d="M2.5 1l2 0 1 2.5-1.3 1a6 6 0 0 0 3.3 3.3l1-1.3 2.5 1v2a1 1 0 0 1-1 1A9.5 9.5 0 0 1 1.5 2a1 1 0 0 1 1-1z" fill="var(--white)"/></svg>
    </li>
    <li>harborlineautoxq@mailnest.example
      <svg class="icon" viewBox="0 0 12 12"><rect x="0.5" y="2" width="11" height="8" rx="1" fill="var(--white)"/><path d="M1 2.5l5 4 5-4" fill="none" stroke="var(--orange)" stroke-width="1"/></svg>
    </li>
    <li>www.harborlineautoxq.net
      <svg class="icon" viewBox="0 0 12 12"><circle cx="6" cy="6" r="5.5" fill="var(--white)"/><path d="M0.5 6h11M6 0.5c-2.5 3-2.5 8 0 11M6 0.5c2.5 3 2.5 8 0 11" fill="none" stroke="var(--orange)" stroke-width="0.8"/></svg>
    </li>
  </ul>
</section>

</body>
</html>
```